Wordpress site for cyber security and network perfomance software vendor

We need a brand new Wordpress website consisting of a single home/landing page and page template so that we can add pages in future.
The website is intended to provide information to prospects and customers. The homepage should have a top menu bar that is customizable similar to what we already have at quillmarsh.com.
Note that we are after a new design – that is, please don’t reference our existing website for design inspiration (quillmarsh.com)
We are after a Wordpress site that may be implemented straight onto our Wordpress hoster (HostPetal) .
Quillmarsh is a software company delivering a solution for customers to get visibility of network performance and cyber security. The Quillmarsh solution reduces cyber security risk, identifies performance bottlenecks and ultimately lower costs by reducing the number of tools need to monitor the IT environment
We deliver network performance and cyber security information to the IT manager and network teams in a format that they understand, at a realistic cost, and requiring minimal resource to implement. This is a crowded market, most competitors provide highly complex, expensive and highly customized tools to large enterprise. Quillmarsh makes this style of visibility tool accessible to the mid market.

Target Market(s)

IT Managers, network engineers, mid market organisations, IT service providers

Industry/Entity Type

IT

Font styles to use
Sans Serif

Colors
0094D4
00A9DD
6FCCEA
C7EBF8
E9F6FB

Requirements
Must have
• Fully coded for WordPress. Responsive and mobile friendly. The website copy is provided in the attached document. Utilise the Quillmarsh logo colors as part of the design (Dark Blue: 2E4F99, Light Blue: 00AFF4, Green: 73D94F). Top Horizontal menu bar for additional pages. Implement one of our screenshots (I have included a bunch of screenshots to choose from)
Nice to have
• Icons, panels or infographics matching the services. Our existing site is built using Divi – this is not a requirement for the new site but a nice to have as we are familiar with Divi.
Should not have
• Preferably no corporate images – business people shaking hands or teams of people a meeting room (or that kind of thing)

```html
<!DOCTYPE html>
<html lang="en">
<head>
<meta charset="utf-8">
<title>Quillmarsh — Security + Visibility</title>
<link href="https://fonts.googleapis.com/css2?family=Roboto:ital,wght@0,400;0,500;0,700;1,400;1,500;1,700&display=swap" rel="stylesheet">
<style>
:root{
  --black:#000;
  --panel:#050608;
  --card-border:#2a2d33;
  --white:#fff;
  --muted:#d9dde3;
  --brand-blue:#0b63b8;
  --brand-blue-dark:#0a4f97;
  --sky:#1e9be0;
  --light-blue:#00aff4;
  --green:#73d94f;
  --link:#2b7fd8;
}
*{margin:0;padding:0;box-sizing:border-box}
html,body{width:1200px;height:4351px;overflow:hidden;background:var(--black)}
body{position:relative;font-family:'Roboto',sans-serif;color:var(--white)}
.abs{position:absolute}
.btn{position:absolute;display:flex;align-items:center;justify-content:center;background:var(--brand-blue);color:var(--white);border-radius:24px;font-size:16px;font-weight:500;text-transform:uppercase;letter-spacing:.2px}

/* nav */
.site-header{position:absolute;left:0;top:0;width:1200px;height:80px;background:var(--black)}
.wordmark{position:absolute;display:flex;align-items:center;gap:10px;color:var(--white);font-weight:400}
.wordmark .dot{border-radius:50%;background:var(--green)}
.main-nav{position:absolute;left:405px;top:30px;display:flex;gap:0;font-size:16px;font-weight:500}
.main-nav a{color:var(--white);text-decoration:none;position:absolute;white-space:nowrap}
.main-nav a.active{color:var(--green)}

/* hero */
.hero{position:absolute;left:0;top:80px;width:1200px;height:735px;
  background:radial-gradient(ellipse 60% 40% at 20% 55%,#1560c9 0%,rgba(10,40,120,.6) 45%,transparent 75%),
  radial-gradient(ellipse 55% 40% at 85% 45%,#1257c0 0%,rgba(10,40,120,.5) 45%,transparent 75%),
  linear-gradient(180deg,#020a2a 0%,#041a5a 55%,#020b2c 100%)}
.hero h1{position:absolute;top:82px;width:100%;text-align:center;font-size:44px;font-weight:700;letter-spacing:.5px}
.hero .lead{position:absolute;top:148px;width:100%;text-align:center;font-size:26px;font-weight:500}
.hero-arrow{position:absolute;top:292px}
.product-shot{position:absolute;left:320px;top:303px;width:558px;height:380px;border-radius:14px;
  background:linear-gradient(180deg,#1f2229 0%,#14171c 100%);border:10px solid #0d0e11}
.product-base{position:absolute;left:258px;top:683px;width:684px;height:10px;border-radius:0 0 10px 10px;background:linear-gradient(180deg,#9aa0a8,#4b5058)}

/* features */
.section-title{position:absolute;width:1200px;text-align:center;font-size:34px;font-weight:700}
.feature-card{position:absolute;width:312px;height:328px;border:1px solid var(--card-border);border-radius:4px;background:var(--panel);text-align:center;padding:0 16px}
.feature-card .icon{width:86px;height:86px;border-radius:50%;background:var(--brand-blue);border:3px solid var(--white);margin:36px auto 0;display:flex;align-items:center;justify-content:center}
.feature-card h3{font-size:20px;font-weight:700;line-height:29px;margin-top:24px}
.feature-card p{font-size:13px;line-height:27.5px;color:var(--muted);margin-top:8px}

/* why */
.why-band{position:absolute;left:0;top:1700px;width:1200px;height:640px}
.why-text{position:absolute;left:642px;top:1822px;width:447px}
.why-text h2{font-size:36px;font-weight:700}
.why-text p{font-size:14px;line-height:28.5px;text-align:justify;margin-top:18px;color:var(--muted)}

/* about */
.about{position:absolute;left:140px;top:2420px;width:450px}
.about h2{font-size:36px;font-weight:700}
.about .tagline{color:var(--link);font-style:italic;font-weight:500;font-size:17px;line-height:29px;margin-top:10px}
.about .q{font-style:italic;font-weight:500;font-size:14px;line-height:26px;margin-top:14px}
.about .body{font-size:14px;line-height:26px;margin-top:14px;color:var(--muted)}

/* cta */
.cta{position:absolute;left:0;top:2895px;width:1200px;height:405px;
  background:radial-gradient(ellipse 45% 60% at 80% 40%,rgba(20,90,170,.55),transparent 70%),radial-gradient(ellipse 40% 60% at 10% 60%,rgba(20,80,150,.45),transparent 70%),linear-gradient(180deg,#041026,#061a38 60%,#030a18)}
.cta h2{position:absolute;top:112px;width:100%;text-align:center;font-size:26px;font-weight:500;line-height:40px;text-transform:uppercase}

/* blog */
.post{position:absolute;top:3410px;width:310px;height:400px;border:1px solid var(--card-border);background:var(--panel)}
.post .thumb{height:203px}
.post h3{font-size:18px;font-weight:500;margin:18px 18px 0}
.post p{font-size:13px;line-height:23.5px;color:var(--muted);margin:10px 18px 0}
.post .more{position:absolute;left:18px;top:368px;font-size:13px;color:var(--link);text-decoration:underline}

/* footer */
.footer-col{position:absolute;top:4033px}
.footer-col h4{font-size:17px;font-weight:700;text-transform:uppercase}
.footer-col ul{list-style:none;margin-top:10px}
.footer-col li{font-size:13px;line-height:27px;color:var(--muted)}
.contact-item{display:flex;gap:9px;font-size:13px;line-height:18px;color:var(--muted);margin-top:10px}
.social{position:absolute;top:4129px;width:38px;height:38px;border:2px solid var(--white);border-radius:50%}
.email{position:absolute;left:768px;top:4080px;width:312px;height:50px;border:1px solid var(--white);border-radius:25px;font-size:13px;color:var(--muted);padding:17px 20px}
.copyright{position:absolute;top:4305px;width:1200px;text-align:center;font-size:13px;color:var(--muted)}
</style>
</head>
<body>

<header class="site-header">
  <div class="wordmark" style="left:112px;top:22px;font-size:30px"><span class="dot" style="width:34px;height:34px"></span>quillmarsh</div>
  <nav class="main-nav">
    <a class="active" style="left:0">HOME</a>
    <a style="left:84px">PRODUCT</a>
    <a style="left:193px">BLOG</a>
    <a style="left:270px">ABOUT</a>
    <a style="left:359px">PARTNER PORTAL</a>
  </nav>
  <span class="btn" style="left:930px;top:18px;width:156px;height:44px">Demo Login</span>
</header>

<section class="hero">
  <h1>SECURITY + VISIBILITY</h1>
  <p class="lead">Network Monitoring for IT Performance and Security</p>
  <span class="btn" style="left:522px;top:207px;width:156px;height:45px">Get Started</span>
  <svg class="hero-arrow" style="left:80px" width="16" height="30" viewBox="0 0 16 30"><path d="M14 2 2 15l12 13" fill="none" stroke="#fff" stroke-width="2"/></svg>
  <svg class="hero-arrow" style="left:1104px" width="16" height="30" viewBox="0 0 16 30"><path d="M2 2l12 13L2 28" fill="none" stroke="#fff" stroke-width="2"/></svg>
  <div class="product-shot" role="img" aria-label="Dashboard screenshot showing traffic bar charts and category donut charts"></div>
  <div class="product-base"></div>
</section>

<h2 class="section-title" style="top:864px">WE DELIVER EVERYTHING YOU NEED</h2>

<div class="feature-card" style="left:110px;top:942px">
  <div class="icon"><svg width="44" height="40" viewBox="0 0 44 40" fill="none" stroke="#fff" stroke-width="2"><rect x="3" y="4" width="38" height="26"/><path d="M9 26V18M16 26V12M23 26V16M30 26V9M16 36h12M22 30v6"/></svg></div>
  <h3>Sophisticated Data Analytics</h3>
  <p>Powerful data analytics correlate threat data and anomalous traffic data with network performance toa deliver meaningful information so you can easily respond.</p>
</div>
<div class="feature-card" style="left:443px;top:942px">
  <div class="icon"><svg width="44" height="40" viewBox="0 0 44 40" fill="none" stroke="#fff" stroke-width="2"><rect x="3" y="5" width="38" height="24" rx="2"/><circle cx="14" cy="17" r="5"/><circle cx="30" cy="17" r="5"/><path d="M14 36h16M22 29v7"/></svg></div>
  <h3>Best Visual Analytics</h3>
  <p>Proactive alerts and dynamic traffic flows are integrated into an intuitive, user friendly dashboard that enable you to plug your visibility blind spots.</p>
</div>
<div class="feature-card" style="left:776px;top:942px">
  <div class="icon"><svg width="40" height="40" viewBox="0 0 40 40" fill="none" stroke="#fff" stroke-width="2"><path d="M6 14h8a4 4 0 1 1 8 0h8v8a4 4 0 1 1 0 8v6H6V28a4 4 0 1 0 0-8z"/></svg></div>
  <h3>Flexible Solutions</h3>
  <p>Our network monitoring AND cyber security solution can be scaled to fit your organisation.</p>
</div>
<div class="feature-card" style="left:278px;top:1293px">
  <div class="icon"><svg width="44" height="40" viewBox="0 0 44 40" fill="none" stroke="#fff" stroke-width="2"><path d="M4 36h36M10 36V20h24v16M14 20v-6h16v6M22 6v8"/><circle cx="22" cy="5" r="3"/></svg></div>
  <h3>Superior Service</h3>
  <p>From first contact through to deployment, our friendly, expert team will discuss your needs and quickly install our easy-to-use platform and tools.</p>
</div>
<div class="feature-card" style="left:611px;top:1293px">
  <div class="icon"><svg width="40" height="40" viewBox="0 0 40 40" fill="none" stroke="#fff" stroke-width="2"><circle cx="18" cy="12" r="7"/><path d="M5 36c0-8 6-13 13-13s13 5 13 13"/><circle cx="30" cy="28" r="6"/><path d="M30 25v6M28 28h4"/></svg></div>
  <h3>Decrease your total cost of ownership</h3>
  <p>The Quillmarsh platform will give you visibility across your network performance AND cyber security data.</p>
</div>

<svg class="why-band" viewBox="0 0 1200 640" preserveAspectRatio="none">
  <path d="M0 10 600 40 1200 0V640L600 610 0 640Z" fill="#0a0b0d"/>
</svg>
<div class="abs" role="img" aria-label="Photo of two analysts working in a network operations centre with large monitoring screens" style="left:0;top:1710px;width:600px;height:625px;clip-path:polygon(0 0,100% 30px,100% 595px,0 100%);background:radial-gradient(ellipse at 25% 30%,#3a8ad8 0%,#1a4c90 40%,#0a2248 80%)"></div>
<div class="why-text">
  <h2>WHY QUILLMARSH?</h2>
  <p>At Quillmarsh, we understand the challenges that you face. Cyber security and network incidents can have devastating impacts on small to medium organisations because you typically don’t have the time, staff, or resources to develop complicated responses to cyber security threats. That’s why small to medium sized organisations are vulnerable to potentially devastating cyber incidents. Did you know that on average, it took over 220 days for organisations to identify a breach and a further 80 days to contain the breach? (Northbeam Research, 2020).</p>
</div>
<span class="btn" style="left:642px;top:2167px;width:156px;height:44px">Learn More</span>

<section class="about">
  <h2>QUILLMARSH</h2>
  <p class="tagline">Specialising in IT Network Performance and Cyber Security Solutions for Small to Medium Organisations.</p>
  <p class="q">Do you feel concerned about your network performance, and cyber threats, but you don’t have the time or staff to deal with it?</p>
  <p class="q">Perhaps you’ve outsourced your IT support and have discovered that your service provider doesn’t have visibility of your network?</p>
  <p class="body">It’s not easy being an IT manager. Especially if you work in a small to medium sized organisation. You’re typically stretched to the limit with an understaffed team and there’s simply not enough hours in the day to tackle all the increasing demands.</p>
</section>
<div class="wordmark" style="left:700px;top:2560px;font-size:52px"><span class="dot" style="width:70px;height:70px;background:var(--light-blue)"></span>quillmarsh</div>

<section class="cta" role="img" aria-label="Abstract blue network connection background">
  <h2>At Quillmarsh, we’re committed to providing you the best<br>easy-to-use tools that will give you visibility, security,<br>and peace of mind.</h2>
  <span class="btn" style="left:514px;top:255px;width:171px;height:43px">Give us a call!</span>
  <svg class="abs" style="left:0;top:330px" width="1200" height="75" viewBox="0 0 1200 75"><path d="M0 50Q600 20 1200 50" fill="none" stroke="#1e6fd0" stroke-width="4"/><path d="M0 62Q600 38 1200 62" fill="none" stroke="#0d3f80" stroke-width="2"/></svg>
</section>

<h2 class="section-title" style="top:3334px">LATEST BLOG</h2>

<article class="post" style="left:110px">
  <div class="thumb" role="img" aria-label="Photo of a hand holding a smartphone in a busy street" style="background:linear-gradient(135deg,#c8d6e6,#7f96b4 50%,#b77468)"></div>
  <h3>Will TLS 1.3 split the Internet?</h3>
  <p>A new version of Transport Layer Security (TLS) is coming... welcome TLS1.3! Well to be fair it is already here and has been for over 12 months, but as is the case</p>
  <span class="more">LEARN MORE »</span>
</article>
<article class="post" style="left:444px">
  <div class="thumb" role="img" aria-label="Photo of a roadside sign reading thank you for driving carefully" style="background:linear-gradient(135deg,#8a9a7a,#5e6b4c 50%,#b4a064)"></div>
  <h3>The Irony of the Corvane Hack</h3>
  <p>I must confess, there was just the slightest sense of schadenfreude when I first heard of the Corvane hack. I mean, Corvane are a behemoth in the network performance</p>
  <span class="more">LEARN MORE »</span>
</article>
<article class="post" style="left:778px">
  <div class="thumb" role="img" aria-label="Photo of stacked metal cylinders" style="background:linear-gradient(135deg,#d6d6d6,#7a7a7a 50%,#3a3a3a)"></div>
  <h3>Will TLS 1.3 split the Internet?</h3>
  <p>Have you ever heard of the term ‘single pane of glass’ when IT people speak about monitoring tools ... of course you have! It’s a oft used (and mis-used) term for a</p>
  <span class="more">LEARN MORE »</span>
</article>

<svg class="abs" style="left:0;top:3900px" width="1200" height="70" viewBox="0 0 1200 70"><path d="M0 20 600 50 1200 20" fill="none" stroke="#1e6fd0" stroke-width="4"/><path d="M0 32 600 62 1200 32" fill="none" stroke="#0d3f80" stroke-width="2"/></svg>

<div class="wordmark" style="left:112px;top:4050px;font-size:34px;color:#1e9be0"><span class="dot" style="width:40px;height:40px"></span>quillmarsh</div>
<span class="social" style="left:111px"></span>
<span class="social" style="left:161px"></span>
<span class="social" style="left:210px"></span>
<span class="social" style="left:259px"></span>

<div class="footer-col" style="left:352px">
  <h4>Explore</h4>
  <ul><li>Home</li><li>&nbsp;Product</li><li>&nbsp;Blog</li><li>&nbsp;About</li><li>&nbsp;Partner Portal</li><li>&nbsp;Demo Login</li></ul>
</div>
<div class="footer-col" style="left:536px;width:210px">
  <h4>Contact Us</h4>
  <div class="contact-item" style="margin-top:14px"><svg width="14" height="18" viewBox="0 0 14 18"><path d="M7 1a6 6 0 0 0-6 6c0 5 6 10 6 10s6-5 6-10a6 6 0 0 0-6-6z" fill="#fff"/><circle cx="7" cy="7" r="2.2" fill="#000"/></svg><span>48 Harbour Lane Anywhere<br>USA 21212</span></div>
  <div class="contact-item"><svg width="14" height="14" viewBox="0 0 14 14"><path d="M3 1 5 4 4 6c1 2 2 3 4 4l2-1 3 2-1 2c-6 0-11-5-11-11z" fill="#fff"/></svg><span>Quillmarsh Australia<br>Ph: +61 2 5550 1420</span></div>
  <div class="contact-item"><svg width="14" height="14" viewBox="0 0 14 14"><path d="M3 1 5 4 4 6c1 2 2 3 4 4l2-1 3 2-1 2c-6 0-11-5-11-11z" fill="#fff"/></svg><span>Quillmarsh Germany<br>Ph: +49 69 555 01 388</span></div>
</div>
<div class="footer-col" style="left:768px">
  <h4>Sign Up For Newsletter</h4>
</div>
<div class="email">Email..</div>
<span class="btn" style="left:768px;top:4141px;width:312px;height:49px;border-radius:25px">Subscribe</span>

<div class="abs" style="left:110px;top:4268px;width:980px;height:1px;background:#2a2d33"></div>
<p class="copyright">Copyright © 2021 quillmarsh. All rights reserved.</p>

</body>
</html>
```